Internet Service Tech provider product flyer redesign - High Rise WIFI

We have created the attached flyer in Word and also attached a PDF. All the content is correct. We just need a complete re-design of the flyer with new relevant hi-res images (based on content) and a more streamlined/cleaner layout.

This product is an entire in-building WIFI system for Body's Corporate in High Rise buildings.

We are a Brisbane-based internet tech company that specialises in providing solutions for High Rise buildings

Body text style - Helvetica Light

Internet

```html
<!DOCTYPE html>
<html lang="en">
<head>
<meta charset="utf-8">
<title>High-Rise WIFI for body's corporate</title>
<link rel="stylesheet" href="https://fonts.googleapis.com/css2?family=Roboto:ital,wght@0,300;0,700;0,900;1,300;1,700&display=swap">
<style>
  :root {
    --teal-dark: #1d4349;
    --teal: #2f6670;
    --ink: #1c3439;
    --sky-top: #c9dbe9;
    --sky-mid: #5f8fb8;
    --glass-deep: #20496f;
    --white: #ffffff;
    --ring: #d6e2e6;
  }
  html, body { margin: 0; padding: 0; overflow: hidden; }
  body { width: 849px; height: 1200px; background: var(--white); }
  .flyer {
    position: relative;
    width: 849px;
    height: 1200px;
    overflow: hidden;
    font-family: "Roboto", "Helvetica Neue", Arial, sans-serif;
  }
  .flyer-art { position: absolute; inset: 0; }
  .headline { position: absolute; margin: 0; line-height: 1; white-space: nowrap; }
  .headline-lead {
    left: 122px; top: 72px;
    font-size: 66px; font-weight: 700; color: var(--white);
    letter-spacing: -1px;
  }
  .headline-main {
    left: 178px; top: 140px;
    font-size: 186px; font-weight: 900; color: var(--ink);
    letter-spacing: 22px;
  }
  .headline-sub {
    left: 262px; top: 306px;
    font-size: 38px; font-weight: 700; color: var(--ink);
  }
  .feature-label {
    position: absolute;
    display: flex; align-items: center; justify-content: center;
    width: 136px; height: 136px;
    border-radius: 50%;
    color: var(--white);
    font-weight: 700; font-size: 21px; line-height: 1.15;
    text-align: center; text-transform: uppercase;
  }
  .feature-text {
    position: absolute; margin: 0;
    font-size: 21px; font-weight: 300; font-style: italic;
    line-height: 1.2; color: var(--ink);
  }
  .feature-bulk .feature-label { left: 420px; top: 655px; }
  .feature-bulk .feature-text { left: 568px; top: 740px; width: 260px; }
  .feature-hd .feature-label { left: 266px; top: 838px; }
  .feature-hd .feature-text { left: 420px; top: 848px; width: 392px; text-align: right; }
  .feature-billing .feature-label { left: 104px; top: 1040px; }
  .feature-billing .feature-text { left: 482px; top: 1070px; width: 330px; }
</style>
</head>
<body>
<main class="flyer">
  <svg class="flyer-art" width="849" height="1200" viewBox="0 0 849 1200">
    <defs>
      <linearGradient id="tower-tones" x1="0" y1="0" x2="0.6" y2="1">
        <stop offset="0" stop-color="#c9dbe9"/>
        <stop offset="0.45" stop-color="#5f8fb8"/>
        <stop offset="1" stop-color="#20496f"/>
      </linearGradient>
    </defs>

    <rect class="building-photo" x="0" y="0" width="849" height="1200" fill="url(#tower-tones)"
          role="img" aria-label="Photo of glass high-rise office towers seen from below against the sky"/>

    <path class="sweep-band" d="M849 40 C780 150 745 290 752 430 L849 430 Z" fill="#1d4349"/>
    <path class="white-field" d="M849 300 C780 360 720 420 670 480 C490 700 270 960 60 1200 L849 1200 Z" fill="#ffffff"/>
    <path class="sweep-edge" d="M849 80 C800 170 785 290 796 420" fill="none" stroke="#ffffff" stroke-width="9"/>

    <path class="feature-chain" d="M650 560 C560 700 330 900 60 1200" fill="none"
          stroke="#2f6670" stroke-width="16" stroke-dasharray="30 14"/>

    <circle class="signal-badge" cx="693" cy="540" r="90" fill="#ffffff" stroke="#d6e2e6" stroke-width="6"/>
    <g class="signal-icon" fill="none" stroke="#1d4349" stroke-width="5" stroke-linecap="round">
      <path d="M693 520 L668 610 M693 520 L718 610 M678 570 L708 570 M673 590 L713 590 M680 555 L706 590 M706 555 L680 590"/>
      <path d="M677 500 A22 22 0 0 1 709 500 M667 490 A36 36 0 0 1 719 490 M657 480 A50 50 0 0 1 729 480"/>
      <circle cx="693" cy="515" r="5" fill="#1d4349"/>
    </g>

    <circle cx="488" cy="723" r="68" fill="#1d4349"/>
    <circle cx="334" cy="906" r="68" fill="#1d4349"/>
    <circle cx="172" cy="1108" r="68" fill="#1d4349"/>
  </svg>

  <h1 class="headline headline-lead">High-Rise</h1>
  <p class="headline headline-main">WIFI</p>
  <p class="headline headline-sub">for body's corporate</p>

  <section class="feature feature-bulk">
    <div class="feature-label">Bulk<br>Supply</div>
    <p class="feature-text">of Fibre-type Internet speeds delivered to all residents at wholesale prices</p>
  </section>
  <section class="feature feature-hd">
    <div class="feature-label">HD WiFi</div>
    <p class="feature-text">designed specifically for high-rise buildings, using next-generation WIFI technology</p>
  </section>
  <section class="feature feature-billing">
    <div class="feature-label">Automated<br>Billing</div>
    <p class="feature-text">and payment system that's simple, easy to use and available 24/7</p>
  </section>
</main>
</body>
</html>
```